Four in One (Flexible infographic for Content Management Industry)

See attachment.
A graphic depicting 4 products, where each can stand on its own and each can be combined with others, but where, if all are taken together, the best result is achieved (the "super product").
Intended use is web. See attached file as an example.
The most basic idea is as the attached diagram shows, where 4 rectangles are arranged in a quadrangle, with a middle rectangle in the center representing the combined 4 products. This concept is fine except it is a bit too obvious as it stands. We are looking for either a variation of this or another concept.
The audience is technical + professional + enterprise - NOT consumers. Hence the design should be conservative in nature.
We are aware of tools like as Canva or Pictogram where such graphics are available, but we are looking for something with a bit more imagination and flexibility.
This graphic should be targeted to web sites and be delivered with vector-based (SVG) graphics.

```html
<!DOCTYPE html>
<html lang="en">
<head>
<meta charset="utf-8">
<title>Four in One – Product Infographic</title>
<link rel="stylesheet" href="https://fonts.googleapis.com/css2?family=Source+Sans+3:wght@400;600;700;800&display=swap">
<style>
  :root {
    --page: #ffffff;
    --panel: #e7e6da;
    --ink: #3e3e3e;
    --muted: #a6a59c;
    --blue-dark: #35a3c1;
    --blue: #17bcd1;
    --red-dark: #dd553b;
    --red: #f15a38;
    --purple: #b05aa5;
    --pink: #e06ea9;
    --green-dark: #68a53e;
    --green: #7dc54b;
    --photo-light: #ffffff;
    --photo-shade: #eceff3;
    --fold: rgba(0, 0, 0, 0.13);
  }
  * { box-sizing: border-box; margin: 0; padding: 0; }
  html, body { width: 1200px; height: 1094px; overflow: hidden; background: var(--page); }
  body { position: relative; font-family: "Source Sans 3", "Myriad Pro", sans-serif; }

  .board { position: absolute; display: grid; overflow: hidden; }
  .board--stacked {
    left: 289px; top: 91px; width: 629px; height: 408px;
    grid-template-columns: 255px 110px 264px;
    grid-template-rows: repeat(4, 102px);
    border-radius: 0 54px 54px 0;
  }
  .board--spread {
    left: 104px; top: 596px; width: 1000px; height: 407px;
    grid-template-columns: 264px 110px 253px 109px 264px;
    grid-template-rows: repeat(2, 203.5px);
    border-radius: 54px;
  }

  .hub { background: var(--panel); grid-row: 1 / -1; position: relative; }
  .board--spread .hub { box-shadow: inset 2px 0 3px var(--fold); }
  .hub__photo {
    position: absolute; left: 38px; top: 40px; width: 179px; height: 199px;
    background: radial-gradient(ellipse at 50% 70%, var(--photo-shade), var(--photo-light) 70%);
  }
  .board--spread .hub__photo { left: 36px; top: 40px; width: 179px; height: 198px; }
  .hub__title {
    position: absolute; left: 0; right: 0; top: 256px; text-align: center;
    font-weight: 700; font-size: 12.5px; color: var(--ink); letter-spacing: 0.1px;
  }
  .hub__body {
    position: absolute; left: 31px; top: 272px; width: 200px;
    font-size: 7.4px; line-height: 8.5px; color: var(--muted);
  }
  .hub__features {
    position: absolute; left: 48px; top: 309px; display: flex; gap: 16px; list-style: none;
  }
  .feature { width: 42px; text-align: center; }
  .feature__icon { display: block; margin: 0 auto; width: 24px; height: 24px; }
  .feature__note { display: block; margin-top: 6px; font-size: 3.2px; line-height: 3.8px; color: var(--muted); }

  .step-number {
    color: #fff; font-weight: 700; font-size: 41px; line-height: 1;
    padding: 14px 0 0 33px; letter-spacing: -0.5px;
  }
  .step-text { color: #fff; padding: 14px 40px 0 34px; }
  .board--spread .step-text--left { padding-left: 44px; }
  .step-text__title { font-weight: 700; font-size: 12px; line-height: 13px; }
  .step-text__body { font-size: 6.6px; line-height: 7.8px; margin-top: 1px; }

  .is-blue.step-number { background: var(--blue-dark); }
  .is-red.step-number { background: var(--red-dark); }
  .is-purple.step-number { background: var(--purple); }
  .is-green.step-number { background: var(--green-dark); }
  .is-blue.step-text { background: linear-gradient(to right, var(--fold), transparent 16px), var(--blue); }
  .is-red.step-text { background: linear-gradient(to right, var(--fold), transparent 16px), var(--red); }
  .is-pink.step-text { background: linear-gradient(to right, var(--fold), transparent 16px), var(--pink); }
  .is-green.step-text { background: linear-gradient(to right, var(--fold), transparent 16px), var(--green); }
  .step-text--left.is-pink { background: linear-gradient(to left, var(--fold), transparent 16px), var(--pink); }
  .step-text--left.is-green { background: linear-gradient(to left, var(--fold), transparent 16px), var(--green); }
  .board--spread .step-number { padding-left: 32px; padding-top: 17px; }
</style>
</head>
<body>

<!-- Stacked layout: hub on the left, four steps in rows -->
<section class="board board--stacked" aria-label="Four products combined, stacked layout">
  <div class="hub">
    <div class="hub__photo" role="img" aria-label="Product photo: white multi-port hub with four coloured flexible arms"></div>
    <h2 class="hub__title">PLACE YOUR TEXT HERE</h2>
    <p class="hub__body">Lorem ipsum dolor sit amet, consectetur adipiscing elit. Etiam ip tum eget leo quis sagittis. Maecenas dapibus ligula at tortor lobo bitur in ex ac ex fringilla varius. Vestibulum condimentum lu</p>
    <ul class="hub__features">
      <li class="feature">
        <svg class="feature__icon" viewBox="0 0 24 24"><circle cx="12" cy="12" r="12" fill="var(--blue-dark)"/><circle cx="12" cy="10" r="2.2" fill="#fff"/><path d="M8 16c0-2.4 1.8-3.6 4-3.6s4 1.2 4 3.6z" fill="#fff"/></svg>
        <span class="feature__note">Short note on<br>this feature</span>
      </li>
      <li class="feature">
        <svg class="feature__icon" viewBox="0 0 24 24"><circle cx="12" cy="12" r="12" fill="var(--red-dark)"/><circle cx="12.8" cy="11" r="2.6" fill="none" stroke="#fff" stroke-width="1.2"/><path d="M11 13l-2.2 2.4" stroke="#fff" stroke-width="1.4" stroke-linecap="round"/></svg>
        <span class="feature__note">Short note on<br>this feature</span>
      </li>
      <li class="feature">
        <svg class="feature__icon" viewBox="0 0 24 24"><circle cx="12" cy="12" r="12" fill="var(--green-dark)"/><path d="M12 7.5l4.5 4h-1.3v4.2h-2.2v-2.6h-2v2.6H8.8v-4.2H7.5z" fill="#fff"/></svg>
        <span class="feature__note">Short note on<br>this feature</span>
      </li>
    </ul>
  </div>

  <div class="step-number is-blue" style="grid-column:2;grid-row:1">01</div>
  <div class="step-text is-blue" style="grid-column:3;grid-row:1">
    <h3 class="step-text__title">PLACE YOUR TEXT HERE</h3>
    <p class="step-text__body">Lorem ipsum dolor sit amet, consectetur adipiscing elit. Etiam ip tum eget leo quis sagittis. Maecenas dapibus ligula at tortor lobo bitur in ex ac ex fringilla varius. Vestibulum condimentum lu</p>
  </div>

  <div class="step-number is-red" style="grid-column:2;grid-row:2">02</div>
  <div class="step-text is-red" style="grid-column:3;grid-row:2">
    <h3 class="step-text__title">PLACE YOUR TEXT HERE</h3>
    <p class="step-text__body">Lorem ipsum dolor sit amet, consectetur adipiscing elit. Etiam ip tum eget leo quis sagittis. Maecenas dapibus ligula at tortor lobo bitur in ex ac ex fringilla varius. Vestibulum condimentum lu</p>
  </div>

  <div class="step-number is-purple" style="grid-column:2;grid-row:3">03</div>
  <div class="step-text is-pink" style="grid-column:3;grid-row:3">
    <h3 class="step-text__title">PLACE YOUR TEXT HERE</h3>
    <p class="step-text__body">Lorem ipsum dolor sit amet, consectetur adipiscing elit. Etiam ip tum eget leo quis sagittis. Maecenas dapibus ligula at tortor lobo bitur in ex ac ex fringilla varius. Vestibulum condimentum lu</p>
  </div>

  <div class="step-number is-green" style="grid-column:2;grid-row:4">04</div>
  <div class="step-text is-green" style="grid-column:3;grid-row:4">
    <h3 class="step-text__title">PLACE YOUR TEXT HERE</h3>
    <p class="step-text__body">Lorem ipsum dolor sit amet, consectetur adipiscing elit. Etiam ip tum eget leo quis sagittis. Maecenas dapibus ligula at tortor lobo bitur in ex ac ex fringilla varius. Vestibulum condimentum lu</p>
  </div>
</section>

<!-- Spread layout: hub in the centre, two steps on each side -->
<section class="board board--spread" aria-label="Four products combined, spread layout">
  <div class="step-text step-text--left is-pink" style="grid-column:1;grid-row:1">
    <h3 class="step-text__title">PLACE YOUR TEXT HERE</h3>
    <p class="step-text__body">Lorem ipsum dolor sit amet, consectetur adipiscing elit. Etiam ip tum eget leo quis sagittis. Maecenas dapibus ligula at tortor lobo bitur in ex ac ex fringilla varius. Vestibulum condimentum lu</p>
  </div>
  <div class="step-number is-purple" style="grid-column:2;grid-row:1">04</div>

  <div class="step-text step-text--left is-green" style="grid-column:1;grid-row:2">
    <h3 class="step-text__title">PLACE YOUR TEXT HERE</h3>
    <p class="step-text__body">Lorem ipsum dolor sit amet, consectetur adipiscing elit. Etiam ip tum eget leo quis sagittis. Maecenas dapibus ligula at tortor lobo bitur in ex ac ex fringilla varius. Vestibulum condimentum lu</p>
  </div>
  <div class="step-number is-green" style="grid-column:2;grid-row:2">03</div>

  <div class="hub" style="grid-column:3">
    <div class="hub__photo" role="img" aria-label="Product photo: white multi-port hub with four coloured flexible arms"></div>
    <h2 class="hub__title">PLACE YOUR TEXT HERE</h2>
    <p class="hub__body">Lorem ipsum dolor sit amet, consectetur adipiscing elit. Etiam ip tum eget leo quis sagittis. Maecenas dapibus ligula at tortor lobo bitur in ex ac ex fringilla varius. Vestibulum condimentum lu</p>
    <ul class="hub__features" style="top:326px;left:44px">
      <li class="feature">
        <svg class="feature__icon" viewBox="0 0 24 24"><circle cx="12" cy="12" r="12" fill="var(--blue)"/><circle cx="12" cy="10" r="2.2" fill="#fff"/><path d="M8 16c0-2.4 1.8-3.6 4-3.6s4 1.2 4 3.6z" fill="#fff"/></svg>
        <span class="feature__note">Short note on<br>this feature</span>
      </li>
      <li class="feature">
        <svg class="feature__icon" viewBox="0 0 24 24"><circle cx="12" cy="12" r="12" fill="var(--red-dark)"/><circle cx="12.8" cy="11" r="2.6" fill="none" stroke="#fff" stroke-width="1.2"/><path d="M11 13l-2.2 2.4" stroke="#fff" stroke-width="1.4" stroke-linecap="round"/></svg>
        <span class="feature__note">Short note on<br>this feature</span>
      </li>
      <li class="feature">
        <svg class="feature__icon" viewBox="0 0 24 24"><circle cx="12" cy="12" r="12" fill="var(--green-dark)"/><path d="M12 7.5l4.5 4h-1.3v4.2h-2.2v-2.6h-2v2.6H8.8v-4.2H7.5z" fill="#fff"/></svg>
        <span class="feature__note">Short note on<br>this feature</span>
      </li>
    </ul>
  </div>

  <div class="step-number is-blue" style="grid-column:4;grid-row:1">01</div>
  <div class="step-text is-blue" style="grid-column:5;grid-row:1">
    <h3 class="step-text__title">PLACE YOUR TEXT HERE</h3>
    <p class="step-text__body">Lorem ipsum dolor sit amet, consectetur adipiscing elit. Etiam ip tum eget leo quis sagittis. Maecenas dapibus ligula at tortor lobo bitur in ex ac ex fringilla varius. Vestibulum condimentum lu</p>
  </div>

  <div class="step-number is-red" style="grid-column:4;grid-row:2">02</div>
  <div class="step-text is-red" style="grid-column:5;grid-row:2">
    <h3 class="step-text__title">PLACE YOUR TEXT HERE</h3>
    <p class="step-text__body">Lorem ipsum dolor sit amet, consectetur adipiscing elit. Etiam ip tum eget leo quis sagittis. Maecenas dapibus ligula at tortor lobo bitur in ex ac ex fringilla varius. Vestibulum condimentum lu</p>
  </div>
</section>

</body>
</html>
```